MRT Property - Business Cards

Looking for a business card & general letterhead, signage etc design for our new logo.

Colours:
000a20
0056a2
00b5ef
0088ce
68cef2

Fonts:
Poppins
Karla

Please keep look and feel of new brand - example in the zip package I sent.

```html
<!DOCTYPE html>
<html lang="en">
<head>
<meta charset="UTF-8">
<title>MRT Property – Business Cards</title>
<link rel="stylesheet" href="https://fonts.googleapis.com/css2?family=Poppins:wght@300;400;600;700&display=swap">
<style>
  :root {
    --ink: #000a20;
    --brand-blue: #0056a2;
    --brand-cyan: #00b5ef;
    --brand-mid: #0088ce;
    --brand-light: #68cef2;
    --white: #ffffff;
    --stage: #e9edf2;
  }
  * { box-sizing: border-box; margin: 0; padding: 0; }
  html, body { width: 1200px; height: 900px; overflow: hidden; }
  body {
    background: var(--stage);
    font-family: "Poppins", sans-serif;
    display: flex;
    flex-direction: column;
    align-items: center;
    justify-content: center;
    gap: 40px;
  }
  .card {
    position: relative;
    width: 700px;
    height: 400px;
    border-radius: 28px;
    background: var(--brand-blue);
    color: var(--white);
    overflow: hidden;
    box-shadow: 0 10px 28px rgba(0, 10, 32, 0.25);
  }

  /* Front */
  .card--front { padding: 48px 52px; }
  .holder__name {
    font-weight: 700;
    font-size: 34px;
    letter-spacing: 1px;
    color: var(--brand-cyan);
    line-height: 1.1;
  }
  .holder__title {
    font-weight: 300;
    font-size: 19px;
    margin-top: 4px;
  }
  .divider {
    position: absolute;
    left: 52px;
    right: 52px;
    top: 270px;
    height: 1px;
    background: var(--brand-cyan);
  }
  .contact {
    list-style: none;
    margin-top: 34px;
    font-weight: 300;
    font-size: 17px;
    line-height: 1.55;
  }
  .contact__item { display: flex; align-items: center; gap: 10px; }
  .contact__icon { width: 14px; height: 14px; flex: none; }
  .brand-name {
    position: absolute;
    right: 56px;
    top: 120px;
    text-align: right;
    font-weight: 700;
    font-size: 62px;
    line-height: 1;
    color: var(--white);
  }
  .brand-name__sub {
    display: block;
    font-size: 20px;
    letter-spacing: 9px;
    margin-top: 6px;
  }
  .address {
    position: absolute;
    right: 56px;
    bottom: 40px;
    text-align: right;
    font-weight: 300;
    font-size: 17px;
    line-height: 1.4;
  }

  /* Back */
  .card--back { display: flex; align-items: flex-end; justify-content: flex-end; padding: 0 60px 60px 0; }
  .pattern-field {
    position: absolute;
    inset: 0;
    background: linear-gradient(135deg, #0a4f98 0%, var(--brand-blue) 45%, #0a6fd0 100%);
  }
  .card--back .brand-name {
    position: relative;
    right: auto;
    top: auto;
    font-size: 46px;
  }
  .card--back .brand-name__sub { font-size: 15px; letter-spacing: 7px; }
</style>
</head>
<body>
  <section class="card card--front" aria-label="Business card front">
    <h1 class="holder__name">DANA MORROW</h1>
    <p class="holder__title">Founder &amp; Principal</p>
    <ul class="contact">
      <li class="contact__item">
        <svg class="contact__icon" viewBox="0 0 16 16" aria-hidden="true"><path d="M4 1.5 6 4 4.8 5.6a9 9 0 0 0 5.6 5.6L12 10l2.5 2-1.3 2.3C7.5 14 2 8.5 1.7 2.8Z" fill="none" stroke="#00b5ef" stroke-width="1.3"/></svg>
        +1- 555-014-2290
      </li>
      <li class="contact__item">
        <svg class="contact__icon" viewBox="0 0 16 16" aria-hidden="true"><rect x="1.5" y="3.5" width="13" height="9" fill="none" stroke="#00b5ef" stroke-width="1.3"/><path d="M1.5 3.5 8 9l6.5-5.5" fill="none" stroke="#00b5ef" stroke-width="1.3"/></svg>
        info@mrtproperty.com
      </li>
      <li class="contact__item">
        <svg class="contact__icon" viewBox="0 0 16 16" aria-hidden="true"><circle cx="8" cy="8" r="6.5" fill="none" stroke="#00b5ef" stroke-width="1.3"/><path d="M1.5 8h13M8 1.5c-3 3.5-3 9.5 0 13M8 1.5c3 3.5 3 9.5 0 13" fill="none" stroke="#00b5ef" stroke-width="1.1"/></svg>
        www.mrtproperty.com
      </li>
    </ul>
    <div class="brand-name">MRT<span class="brand-name__sub">PROPERTY</span></div>
    <div class="divider"></div>
    <p class="address">4210 North Elm Avenue<br>#12, Suite Ridgeview</p>
  </section>

  <section class="card card--back" aria-label="Business card back">
    <div class="pattern-field" role="img" aria-label="Repeating brand pattern in tones of blue"></div>
    <div class="brand-name">MRT<span class="brand-name__sub">PROPERTY</span></div>
  </section>
</body>
</html>
```